Business card design Needed for new logo / Construction business, home extensions and new builds

We need a business card design using our new logo files which i will attach to this project :)

We are a small construction business specialising in home extensions, new builds and property development. We are very ambitious and would appreciate professional and elegant designs for our new business card.

Very serious about using the services on MakerQuarry and recently acquired our new logo from here :)

Please get involved, i will feedback when i can as i am very busy but can respond daily, thanks

Target Market(s)

People that want to build onto their houses, new building developments or adding too their existing property

Industry/Entity Type

Construction

Contact Information for Business Card

Renwick Tolliver Construction, Lionel Ashby (Managing Director), Tel 07822254961, email - info@renwick-tolliver, www.renwick-tolliver.co.uk

Colors

Designer to choose colors to be used in the design.

Requirements
Must have
• I like a deep grey on the back please. A lot of you have provided black from and back, try mixing things up a little. The black looks cool 😎 Thanks

```html
<!DOCTYPE html>
<html lang="en">
<head>
<meta charset="utf-8">
<title>Renwick Tolliver Construction – Business Card</title>
<link href="https://fonts.googleapis.com/css2?family=Cinzel:wght@500;600&family=Montserrat:wght@500;600;800&display=swap" rel="stylesheet">
<style>
  :root {
    --backdrop: #232324;
    --card-front: #1b1b1c;
    --card-back: #3a3b3d;
    --gold: #d9a12e;
    --silver: #d6d8da;
    --panel: #ffffff;
    --ink: #222222;
  }
  * { margin: 0; padding: 0; box-sizing: border-box; }
  html, body { width: 1200px; height: 875px; overflow: hidden; }
  body {
    background: var(--backdrop);
    position: relative;
    font-family: "Montserrat", sans-serif;
  }
  .card {
    position: absolute;
    width: 540px;
    height: 310px;
    border-radius: 16px;
    overflow: hidden;
    box-shadow: 0 18px 40px rgba(0,0,0,.45);
  }

  /* Back of card — deep grey */
  .card-back { left: 50px; top: 110px; background: var(--card-back); }
  .back-brand {
    position: absolute;
    left: 0; right: 0; top: 92px;
    display: flex; align-items: center; justify-content: center; gap: 14px;
  }
  .brand-square { width: 18px; height: 18px; background: var(--gold); flex: none; }
  .back-brand .brand-name {
    font-family: "Cinzel", serif;
    font-weight: 600;
    font-size: 34px;
    letter-spacing: 2px;
    color: var(--gold);
  }
  .back-web {
    position: absolute;
    left: 0; right: 0; top: 200px;
    text-align: center;
    font-family: "Cinzel", serif;
    font-weight: 500;
    font-size: 13px;
    letter-spacing: 3px;
    color: var(--gold);
  }

  /* Front of card */
  .card-front { left: 610px; top: 455px; background: var(--card-front); }
  .front-panel { position: absolute; inset: 0; }
  .front-brand {
    position: absolute; left: 34px; top: 70px;
    display: flex; align-items: flex-start; gap: 12px;
  }
  .front-brand .brand-square { width: 14px; height: 14px; margin-top: 6px; }
  .front-brand .brand-name {
    font-family: "Cinzel", serif;
    font-weight: 600;
    font-size: 21px;
    line-height: 1.25;
    letter-spacing: 1px;
    color: var(--silver);
  }
  .person { position: absolute; left: 34px; top: 196px; }
  .person-name {
    font-weight: 800; font-size: 26px; letter-spacing: .5px;
    color: var(--silver);
  }
  .person-role {
    font-weight: 600; font-size: 15px; color: var(--gold);
    margin-top: 2px;
  }
  .contact-list {
    position: absolute; right: 22px; top: 92px;
    list-style: none;
  }
  .contact-list li {
    display: flex; align-items: center; justify-content: flex-end; gap: 8px;
    font-weight: 500; font-size: 11.5px; color: var(--ink);
    height: 21px;
    white-space: nowrap;
  }
  .contact-list svg { width: 11px; height: 11px; fill: var(--gold); flex: none; }
</style>
</head>
<body>

<section class="card card-back" aria-label="Card back">
  <div class="back-brand">
    <span class="brand-square"></span>
    <span class="brand-name">RENWICK TOLLIVER</span>
  </div>
  <p class="back-web">WWW.RENWICK-TOLLIVER.CO.UK</p>
</section>

<section class="card card-front" aria-label="Card front">
  <svg class="front-panel" viewBox="0 0 540 310" preserveAspectRatio="none" aria-hidden="true">
    <defs>
      <linearGradient id="silverEdge" x1="0" y1="0" x2="1" y2="1">
        <stop offset="0" stop-color="#f2f3f4"/>
        <stop offset=".5" stop-color="#9da1a5"/>
        <stop offset="1" stop-color="#e4e6e8"/>
      </linearGradient>
    </defs>
    <polygon points="345,0 540,0 540,310 296,310" fill="url(#silverEdge)"/>
    <polygon points="354,0 540,0 540,310 306,310" fill="#ffffff"/>
  </svg>

  <div class="front-brand">
    <span class="brand-square"></span>
    <p class="brand-name">RENWICK TOLLIVER<br>CONSTRUCTION</p>
  </div>

  <div class="person">
    <p class="person-name">LIONEL ASHBY</p>
    <p class="person-role">Managing Director</p>
  </div>

  <ul class="contact-list">
    <li>07822 254961 <svg viewBox="0 0 12 12"><path d="M2 1h3l1 3-1.5 1a7 7 0 0 0 2.5 2.5L8 6l3 1v3c0 .6-.4 1-1 1A9 9 0 0 1 1 2c0-.6.4-1 1-1z"/></svg></li>
    <li>07822 254970 <svg viewBox="0 0 12 12"><path d="M3.5 0h5c.6 0 1 .4 1 1v10c0 .6-.4 1-1 1h-5c-.6 0-1-.4-1-1V1c0-.6.4-1 1-1zm.5 2v7h4V2zm2 8a.6.6 0 1 0 0 1.2A.6.6 0 0 0 6 10z"/></svg></li>
    <li>01632 960418 <svg viewBox="0 0 12 12"><path d="M3 0h5v3H3zM1 4h10v5H9v3H3V9H1zm3 3v4h4V7z"/></svg></li>
    <li>info@renwick-tolliver.co.uk <svg viewBox="0 0 12 12"><path d="M0 2h12v8H0zm1 1v.3l5 3.2 5-3.2V3z"/></svg></li>
    <li>www.renwick-tolliver.co.uk <svg viewBox="0 0 12 12"><path d="M6 0a6 6 0 1 0 0 12A6 6 0 0 0 6 0zm0 1.2a4.8 4.8 0 1 1 0 9.6 4.8 4.8 0 0 1 0-9.6zM1.5 5.5h9v1h-9zM5.5 1.5h1v9h-1z"/></svg></li>
    <li>Your Address, City, State <svg viewBox="0 0 12 12"><path d="M6 0a4 4 0 0 1 4 4c0 3-4 8-4 8S2 7 2 4a4 4 0 0 1 4-4zm0 2.5a1.5 1.5 0 1 0 0 3 1.5 1.5 0 0 0 0-3z"/></svg></li>
  </ul>
</section>

</body>
</html>
```